New Webpage for High Class Expert Witness Services Company

We are looking for a minimalist design for a webpage that just has our logo and an entry form offer to connect with one of our Liaisons.
The entry form should just ask for Name, Email, Contact Info and Description of Project.

Company Name is: The Marlowe Crest Advisory Services

Number of Pages Required

1 page

```html
<!DOCTYPE html>
<html lang="en">
<head>
<meta charset="utf-8">
<title>Marlowe Crest Advisory Services</title>
<link href="https://fonts.googleapis.com/css2?family=Cinzel:wght@400;700&family=Manrope:wght@400&family=Roboto:wght@400&display=swap" rel="stylesheet">
<style>
  :root {
    --bg-deep: #0b0b0b;
    --text-light: #f2f2f2;
    --text-heading: #c4c4c4;
    --text-eyebrow: #8c8c8c;
    --text-body: #d8d8d8;
    --text-footer: #9a9a9a;
    --line: #8a8a8a;
    --line-faint: #4a4a4a;
    --button-a: #d9d9da;
    --button-b: #a9a9ac;
    --button-text: #111111;
  }
  * { box-sizing: border-box; margin: 0; padding: 0; }
  html, body { width: 1200px; height: 741px; overflow: hidden; background: var(--bg-deep); }
  .page { position: relative; width: 1200px; height: 741px; overflow: hidden; }
  .hero-photo {
    position: absolute; inset: 0;
    background:
      radial-gradient(ellipse 420px 340px at 520px 300px, rgba(90,90,90,.55), transparent 70%),
      radial-gradient(ellipse 500px 400px at 1050px 420px, rgba(80,80,80,.5), transparent 70%),
      linear-gradient(90deg, #060606 0%, #1e1e1e 45%, #2c2c2c 75%, #323232 100%);
  }
  .brand {
    position: absolute; left: 80px; top: 58px;
    display: flex; align-items: center; gap: 12px;
    font-family: "Cinzel", serif; font-weight: 400; font-size: 22px;
    color: var(--text-light); letter-spacing: 1px;
  }
  .brand-mark { width: 26px; height: 26px; background: var(--text-light); }
  .intro { position: absolute; left: 84px; top: 222px; width: 540px; }
  .eyebrow {
    font-family: "Cinzel", serif; font-size: 19px; letter-spacing: 2px;
    color: var(--text-eyebrow); white-space: nowrap;
  }
  .headline {
    margin-top: 10px;
    font-family: "Cinzel", serif; font-weight: 400; font-size: 46px; line-height: 51px;
    color: var(--text-heading);
  }
  .lede {
    margin-top: 16px; margin-left: 2px;
    font-family: "Manrope", sans-serif; font-size: 15px; line-height: 28px;
    color: var(--text-body);
  }
  .contact-card {
    position: absolute; left: 746px; top: 106px; width: 379px; height: 489px;
    border: 1px solid var(--line); background: rgba(40,40,40,.25);
  }
  .contact-title {
    position: absolute; left: 44px; top: 34px;
    font-family: "Cinzel", serif; font-weight: 400; font-size: 25px; line-height: 30px;
    color: var(--text-light);
  }
  .field-label {
    position: absolute; left: 44px;
    font-family: "Roboto", sans-serif; font-size: 13px; line-height: 16px;
    color: var(--text-light);
  }
  .field-input {
    position: absolute; left: 44px; width: 294px; height: 38px;
    border: 1px solid var(--line); background: transparent;
  }
  .field-area { height: 69px; }
  .submit-button {
    position: absolute; left: 43px; top: 404px; width: 297px; height: 44px;
    border: none;
    background: linear-gradient(100deg, var(--button-a) 0%, #e2e2e3 35%, var(--button-b) 60%, #bdbdc0 100%);
    font-family: "Cinzel", serif; font-weight: 700; font-size: 15px; letter-spacing: .5px;
    color: var(--button-text);
  }
  .site-footer {
    position: absolute; left: 0; right: 0; top: 679px; height: 62px;
    border-top: 1px solid var(--line-faint);
    display: flex; align-items: center; justify-content: center;
    font-family: "Roboto", sans-serif; font-size: 12.5px; color: var(--text-footer);
  }
</style>
</head>
<body>
<div class="page">
  <div class="hero-photo" role="img" aria-label="Black and white photo of two hands meeting in a high five"></div>

  <div class="brand">
    <span class="brand-mark"></span>
    <span class="brand-name">Marlowe Crest Advisory Services</span>
  </div>

  <section class="intro">
    <p class="eyebrow">MARLOWE CREST ADVISORY SERVICES</p>
    <h1 class="headline">SEAMLESS MEDICAL<br>EXPERT INTEGRATION</h1>
    <p class="lede">Lorem ipsum dolor sit amet, consectetur adipiscing elit, sed do eiusmod tempor incididunt ut labore et dolore magna aliqua.</p>
  </section>

  <form class="contact-card">
    <h2 class="contact-title">CONNECT WITH US</h2>
    <label class="field-label" style="top:81px">Name*</label>
    <div class="field-input" style="top:103px"></div>
    <label class="field-label" style="top:153px">Email*</label>
    <div class="field-input" style="top:173px"></div>
    <label class="field-label" style="top:220px;left:41px">Phone number*</label>
    <div class="field-input" style="top:241px"></div>
    <label class="field-label" style="top:291px;left:42px">Description of Project</label>
    <div class="field-input field-area" style="top:313px;left:43px"></div>
    <button type="button" class="submit-button">SUBMIT</button>
  </form>

  <footer class="site-footer">© 2026 Marlowe Crest Advisory Services. All Rights Reserved</footer>
</div>
</body>
</html>
```